Business Card Design for Software Development Company

I am looking for a business card design the incorporates my new logo (attached below).

Key information to include:
Name: Martin Quelbrook
Title: CEO
Email: martin@brightwellcivic.example
Phone: 555-218-9403
Website: www.brightwellcivic.example

NOTE: This design should be easy to edit so that we can order cards for different members of our team.

```html
<!DOCTYPE html>
<html lang="en">
<head>
<meta charset="utf-8">
<title>Brightwell Civic Business Card</title>
<link rel="stylesheet" href="https://fonts.googleapis.com/css2?family=Montserrat:wght@400;500;700&display=swap">
<style>
  :root {
    --bg: #2a2a2a;
    --paper: #f7f7f5;
    --ink: #1d1d1d;
    --teal: #17a895;
    --orange: #e87d2a;
    --orange-soft: #f3b27a;
    --red: #a9202a;
    --rust: #d9502a;
    --white: #ffffff;
  }
  * { box-sizing: border-box; margin: 0; padding: 0; }
  html, body { width: 1200px; height: 801px; overflow: hidden; }
  body {
    background: var(--bg);
    font-family: "Montserrat", sans-serif;
    display: flex;
    align-items: center;
    justify-content: center;
    gap: 40px;
  }
  .card {
    width: 540px;
    height: 309px;
    border-radius: 16px;
    position: relative;
    overflow: hidden;
  }

  /* Company name */
  .company {
    display: flex;
    align-items: center;
    gap: 10px;
  }
  .company-mark {
    width: 12px;
    height: 12px;
    flex: none;
  }
  .company-name {
    font-weight: 500;
    white-space: nowrap;
  }

  /* Front */
  .card-front { background: var(--paper); }
  .front-company {
    position: absolute;
    left: 40px;
    top: 0;
    bottom: 12px;
    width: 220px;
  }
  .front-company .company-mark { background: var(--orange); }
  .front-company .company-name {
    font-size: 22px;
    color: var(--ink);
  }
  .divider {
    position: absolute;
    left: 272px;
    top: 78px;
    width: 1.5px;
    height: 140px;
    background: var(--teal);
  }
  .contact {
    position: absolute;
    left: 292px;
    top: 80px;
  }
  .person-name {
    font-weight: 700;
    font-size: 22px;
    line-height: 1.1;
  }
  .person-name .first { color: var(--teal); }
  .person-name .last { color: var(--orange); }
  .person-title {
    font-size: 13px;
    color: var(--ink);
    margin-bottom: 14px;
  }
  .contact-list { list-style: none; }
  .contact-list li {
    display: flex;
    align-items: center;
    gap: 7px;
    font-size: 11.5px;
    color: var(--ink);
    line-height: 1.7;
  }
  .contact-list svg { width: 9px; height: 9px; flex: none; }
  .edge-band {
    position: absolute;
    left: 0; right: 0; bottom: 0;
    height: 10px;
    display: flex;
  }
  .edge-band span { flex: 1; }
  .edge-band .teal { background: var(--teal); flex: 1.6; }
  .edge-band .red { background: var(--red); }
  .edge-band .rust { background: var(--rust); }
  .edge-band .orange { background: var(--orange); flex: 1.4; }
  .edge-band .soft { background: var(--orange-soft); }

  /* Back */
  .card-back { background: var(--orange); }
  .back-graphic {
    position: absolute;
    left: 30px;
    top: 0;
    width: 150px;
    height: 100%;
    background: linear-gradient(170deg, var(--rust) 0%, var(--orange-soft) 55%, var(--white) 100%);
    opacity: 0.85;
  }
  .back-company {
    position: absolute;
    right: 34px;
    bottom: 80px;
  }
  .back-company .company-mark {
    width: 16px;
    height: 16px;
    background: var(--white);
  }
  .back-company .company-name {
    font-size: 36px;
    color: var(--white);
  }
</style>
</head>
<body>
  <section class="card card-front" aria-label="Business card front">
    <div class="company front-company">
      <span class="company-mark" aria-hidden="true"></span>
      <span class="company-name">Brightwell Civic</span>
    </div>
    <div class="divider"></div>
    <div class="contact">
      <h1 class="person-name"><span class="first">Martin</span> <span class="last">Quelbrook</span></h1>
      <p class="person-title">CEO</p>
      <ul class="contact-list">
        <li>
          <svg viewBox="0 0 10 10" aria-hidden="true"><path d="M2 1l2 2-1 1.2c.6 1.2 1.6 2.2 2.8 2.8L7 6l2 2-1.2 1.5C4.5 9 1 5.5.5 2.2z" fill="var(--orange)"/></svg>
          555-218-9403
        </li>
        <li>
          <svg viewBox="0 0 10 10" aria-hidden="true"><rect x="0.5" y="2" width="9" height="6.5" rx="1" fill="var(--orange)"/><path d="M1 2.5l4 3 4-3" stroke="#fff" stroke-width="0.8" fill="none"/></svg>
          martin@brightwellcivic.example
        </li>
        <li>
          <svg viewBox="0 0 10 10" aria-hidden="true"><circle cx="5" cy="5" r="4.5" fill="var(--orange)"/><path d="M.5 5h9M5 .5c-2 2.5-2 6.5 0 9M5 .5c2 2.5 2 6.5 0 9" stroke="#fff" stroke-width="0.6" fill="none"/></svg>
          www.brightwellcivic.example
        </li>
      </ul>
    </div>
    <div class="edge-band" aria-hidden="true">
      <span class="teal"></span><span class="red"></span><span class="rust"></span><span class="orange"></span><span class="soft"></span>
    </div>
  </section>

  <section class="card card-back" aria-label="Business card back">
    <div class="back-graphic" role="img" aria-label="Large brand symbol decoration in orange, rust and cream tones"></div>
    <div class="company back-company">
      <span class="company-mark" aria-hidden="true"></span>
      <span class="company-name">Brightwell Civic</span>
    </div>
  </section>
</body>
</html>
```